Wordpress Theme for Cedarpoint Clinics

** Please view updated Sitemap2.pdf doc to clarify some confusion ***

This is a multiuser WordPress subscription site for Cedarpoint Clinics. Please see attachment for sitemap. Please do not include extra content like social media icons, search bars, or images. If you have questions, please ask for clarification.
The site contains the following pages and sub-pages:

1. Home
2. Our Clinic
2a. Our Clinic > Mission
2b. Our Clinic > Services
2c. Our Clinic > Clinic Policies
2d. Our Clinic > Schedules
3. Our Staff
3a. Our Staff > [Staff member page]
4. Resources
4a. Resources > Patient Health (index)
4b. Resources > Patient Health (index) > [post]
4c. Resources > Links
4d. Resources > Forms
5. Alerts
5a. Alerts > [Alert Page]
6. Contact Us

Includes the Following Pages, Subpages, and Content
1. Home
a. About Us
b. Our Staff
c. Bulletins
d. Accepting New Patients (shown as an alert widget)
e. Links
i. Physician Toolbox
ii. Book an Appointment
f. Clinic Policies
i. Show first 3 policies (e.g. Late Arrivals, Missed Appointments, Fees)
ii. Link to Clinic Policies page
g. Primary widget (displayed on all pages)
i. Hours of operation
ii. Contact Info
1. Tel
2. Fax
3. Email
4. Address
5. Get directions (link to Google Maps)
2. Our Clinic
a. Main Page
i. Clinic Name
ii. Overview
iii. Languages Spoken
iv. Secondary Navigation
1. Mission
2. Services
3. Clinic Policies
4. Schedules (see attachment)
b. Our Clinic > Mission
c. Our Clinic > Services
i. For each service include service TITLE and DESCRIPTION
d. Our Clinic > Clinic Policies
i. For each policy include policy TITLE and DESCRIPTION
ii. Include the following policies in mockup
1. Late arrivals
2. Missed appointments
3. Fees for missed appointments
4. Referrals and follow-ups
5. Services not covered by RDA
6. Information for LTF patients
7. Medical Legal Reports
e. Our Clinic > Schedules
3. Our Staff
a. Main Page
i. Display a list of staff members. Include NAME and DESIGNATION
b. Our Staff > [Staff Name]
i. Include NAME, PICTURE, DESIGNATION, and BIO
4. Resources
a. Resources > Patient Health
i. Main Page
1. Posts (ordered by date)
a. Title
b. Summary
2. Side Navigation
a. Post Categories
ii. Patient Health > [post title]
1. Title
2. Post Category
3. Date
4. Author
5. Summary
6. Body
b. Resources > Links
1. Secondary Navigation - Categories
a. Sample Categories:
i. Local Services
ii. RDA and Drug Coverage
iii. Mental Health Resources
2. Category page
a. Include the following links in the 'Local Services' category
i. Hypertension clinics
ii. Home Care services
iii. Vaccine Clinics
c. Resources > Forms
i. Display a table with form TITLE and CATEGORY
ii. Side Navigation
1. Form Categories
a. Use the following sample Categories
i. Referrals
ii. Insurance
iii. Intake
iv. Discharge
v. Waivers
5. Alerts
a. Main page
i. List of all Alert posts
1. Include post TITLE as a link to the post
ii. Side Navigation
1. Alerts Archive
a. shown as Month + Number of posts
iii. Alerts > [Alert page]
1. Include TITLE, DATE, AUTHOR, BODY
6. Contact Us
a. Map
b. Hours of operation
c. Address
d. Phone number
e. Fax number
e. Fax number
f. Map
g. Email

Design notes:
- fixed width
- responsive (need designs for mobile, tablet, and desktop)
- simple, dark font, white background
- use Font Awesome icons where needed
- user adds own logo

Target Market(s)

Cedarpoint Clinics

Industry/Entity Type

Medical

Number of Pages Required

5+ page

Font styles to use
Serif
Sans Serif

Requirements
Must have
• Please keep designs very simple.
• Examples:
• https://www.quolbin.com/install
• http://www.ventrohax.com/company/about-us
• http://brindlequota.org/
• http://www.trosk.com/
Should not have
• Minimal or no use of shadows and gradients

```html
<!DOCTYPE html>
<html lang="en">
<head>
<meta charset="utf-8">
<title>Our Staff – Cedarpoint Clinics</title>
<link href="https://fonts.googleapis.com/css2?family=Open+Sans:wght@400;600;700&family=Raleway:wght@500;600&display=swap" rel="stylesheet">
<style>
:root{
  --blue:#0a8be0;
  --blue-link:#1a7fd0;
  --ink:#333;
  --muted:#666;
  --line:#cfcfcf;
  --band:#f7f7f7;
  --footer:#262626;
  --footer-bottom:#222;
  --footer-text:#8a8a8a;
  --footer-head:#9a9a9a;
}
*{box-sizing:border-box;margin:0;padding:0}
html,body{width:1200px;height:1083px;overflow:hidden;background:#fff}
body{font-family:"Open Sans",Arial,sans-serif;color:var(--ink);position:relative}
a{text-decoration:none;color:inherit}
.wrap{position:absolute;left:161px;width:878px}

.topbar{position:absolute;top:0;left:0;width:1200px;height:30px;background:var(--blue);color:#fff;font-size:9.5px}
.topbar .left{position:absolute;left:161px;top:9px}
.topbar .left span+span{border-left:1px solid #fff;margin-left:5px;padding-left:5px}
.topbar .right{position:absolute;right:161px;top:9px}
.topbar .right a+a{border-left:1px solid #fff;margin-left:6px;padding-left:6px}

.header{position:absolute;top:30px;left:0;width:1200px;height:83px}
.brand{position:absolute;left:162px;top:28px;display:flex;align-items:center;gap:12px;font-family:"Open Sans",Arial,sans-serif;font-weight:600;font-size:21px;color:var(--ink)}
.brand .dot{width:22px;height:22px;border-radius:50%;background:var(--blue)}
.nav{position:absolute;right:161px;top:0;display:flex;height:83px;font-size:10.5px}
.nav a{display:flex;align-items:center;padding:0 21px;color:#333}
.nav a:last-child{padding-right:0}
.nav a.active{background:var(--blue);color:#fff;padding:0 9px;margin:0 10px}

.crumbs{position:absolute;top:113px;left:0;width:1200px;height:59px;background:var(--band)}
.crumbs h2{position:absolute;left:162px;top:16px;font-size:10px;font-weight:700;color:#222}
.crumbs p{position:absolute;left:162px;top:35px;font-size:9.5px;color:#333}

.section-title{top:216px;font-size:14px;font-weight:600;letter-spacing:.3px;color:#333}
.section-title::after{content:"";display:block;width:90px;height:2px;background:#ddd;margin-top:8px}

.tabs{top:267px;display:flex;gap:27px;font-size:10.5px}
.tabs a{padding-bottom:5px;border-bottom:2px solid #ddd;color:#333}
.tabs a.current{color:var(--blue-link);font-weight:700;border-color:var(--blue)}

.grid{top:309px;display:grid;grid-template-columns:repeat(4,203px);column-gap:22px;row-gap:23px}
.card{height:240px}
.photo{height:187px;background:linear-gradient(180deg,#fbfbfb 0%,#f2f3f5 55%,#e9edf1 100%)}
.info{height:53px;border:1px solid var(--line);padding:9px 7px 0;background:#fff}
.info h3{font-size:12px;font-weight:600;color:#555}
.info p{font-size:10.5px;color:var(--blue-link);margin-top:3px}

.footer{position:absolute;top:855px;left:0;width:1200px;height:192px;background:var(--footer);border-top:4px solid var(--blue)}
.footer .brand{top:40px;color:#fff}
.footer .about{position:absolute;left:162px;top:89px;width:210px;font-size:8.5px;line-height:14px;color:#bbb}
.fcol{position:absolute;top:37px;font-size:9.5px;color:var(--footer-text)}
.fcol h4{font-size:12.5px;font-weight:700;color:var(--footer-head);margin-bottom:9px}
.fcol li{list-style:none;line-height:18px}
.fcol li.on{color:#ddd}
.contact dl{display:grid;grid-template-columns:89px 1fr;line-height:15px;padding-left:2px}
.bottombar{position:absolute;top:1047px;left:0;width:1200px;height:36px;background:var(--footer-bottom);border-top:1px solid #444;font-size:9.5px;color:var(--footer-text)}
.bottombar span{position:absolute;top:11px}
</style>
</head>
<body>

<div class="topbar">
  <div class="left"><span>To help Here : 111 480 2719</span><span>Email : hello@ cedarpoint.example</span></div>
  <div class="right"><a href="#">Book an Appointment</a><a href="#">Physician Toolbox</a></div>
</div>

<header class="header">
  <div class="brand"><span class="dot"></span>Cedarpoint Clinics</div>
  <nav class="nav">
    <a href="#">Home</a><a href="#">Our Clinic</a><a href="#">Newsletter</a><a href="#" class="active">Our Staff</a><a href="#">Resources</a><a href="#">Contact Us</a>
  </nav>
</header>

<div class="crumbs"><h2>OUR STAFF</h2><p>HOME / OUR STAFF</p></div>

<h1 class="wrap section-title">OUR STAFF</h1>

<div class="wrap tabs">
  <a href="#" class="current">All Departments</a><a href="#">Primary Health Care</a><a href="#">Pediatric Clinic</a><a href="#">Outpatient Surgery</a><a href="#">Cardiac Clinic</a>
</div>

<div class="wrap grid">
  <div class="card"><div class="photo" role="img" aria-label="Portrait of a female doctor in a white coat with stethoscope"></div><div class="info"><h3>Dr. Elena Marsh</h3><p>Pediatric Clinic</p></div></div>
  <div class="card"><div class="photo" role="img" aria-label="Portrait of a male doctor in a white coat and red tie"></div><div class="info"><h3>Dr. Owen Pratley</h3><p>Cardiac Clinic</p></div></div>
  <div class="card"><div class="photo" role="img" aria-label="Portrait of a female doctor in green scrubs with stethoscope"></div><div class="info"><h3>Dr. Lena Voskuil</h3><p>Rehabilitation Therapy</p></div></div>
  <div class="card"><div class="photo" role="img" aria-label="Portrait of a male doctor in a white coat with stethoscope"></div><div class="info"><h3>Dr. Tomas Breckin</h3><p>Laryngological Clinic</p></div></div>
  <div class="card"><div class="photo" role="img" aria-label="Portrait of a female doctor in green scrubs with stethoscope"></div><div class="info"><h3>Dr. Elena Marsh</h3><p>Pediatric Clinic</p></div></div>
  <div class="card"><div class="photo" role="img" aria-label="Portrait of a male doctor in a white coat with stethoscope"></div><div class="info"><h3>Dr. Owen Pratley</h3><p>Cardiac Clinic</p></div></div>
  <div class="card"><div class="photo" role="img" aria-label="Portrait of a female doctor in a white coat with stethoscope"></div><div class="info"><h3>Dr. Lena Voskuil</h3><p>Rehabilitation Therapy</p></div></div>
  <div class="card"><div class="photo" role="img" aria-label="Portrait of a male doctor in a white coat and red tie"></div><div class="info"><h3>Dr. Tomas Breckin</h3><p>Laryngological Clinic</p></div></div>
</div>

<footer class="footer">
  <div class="brand"><span class="dot"></span>Cedarpoint Clinics</div>
  <p class="about">Lorem Ipsum is simply dummy text of the printing and typesetting industry. Lorem Ipsum has been the industry's standard dummy text</p>
  <div class="fcol" style="left:461px"><h4>Navigation</h4><ul><li class="on">Home</li><li>Our Clinic</li><li>Newsletter</li><li>Our Staff</li><li>Resources</li></ul></div>
  <div class="fcol" style="left:686px"><h4>Links</h4><ul><li>Help</li><li>Support</li><li>Privacy Policy</li></ul></div>
  <div class="fcol contact" style="left:836px"><h4>Contact Us</h4>
    <dl><dt>Telephone :</dt><dd>604-555-0182</dd><dt>Email:</dt><dd>hello@cedarpoint.example</dd><dt>Address:</dt><dd>48 Alder Row<br>Fernvale, B. Canada,<br>V0X 2K7</dd></dl>
  </div>
</footer>
<div class="bottombar">
  <span style="left:162px">© 2015 Cedarpoint Clinics. All Rights Reserved</span>
  <span style="left:463px">About Us</span><span style="left:530px">Terms of Use</span><span style="left:615px">Privacy Policy</span>
  <span style="right:164px">Site design &amp; developed by Northgrain Web Studio</span>
</div>

</body>
</html>
```